Northfield Builders Guild Business card

We are looking for a new business card design with photo included.
Our business is a nonprofit construction contractor membership organization. We offer business education, assist with business setup and licensing, provide safety training, and provide a member directory.
URL: www.builderslinkguild.org
Color code:
CMYK: 0 cyan, 42 magenta, 100 yellow, 0 black for Print.
Hexidecimal: #FF9900
RGB: R 255; G 153; B 0

```html
<!DOCTYPE html>
<html lang="en">
<head>
<meta charset="utf-8">
<title>Northfield Builders Guild – Business Card</title>
<link href="https://fonts.googleapis.com/css2?family=Jost:wght@400;700&display=swap" rel="stylesheet">
<style>
  :root {
    --backdrop: #8c8c8c;
    --paper: #ffffff;
    --charcoal: #353334;
    --orange: #ff9900;
    --emboss: #6e6c6d;
  }
  html, body {
    margin: 0;
    padding: 0;
    width: 1200px;
    height: 1200px;
    overflow: hidden;
    background: var(--backdrop);
    font-family: "Jost", sans-serif;
  }
  .canvas {
    position: relative;
    width: 1200px;
    height: 1200px;
  }
  .card {
    position: absolute;
    left: 262px;
    width: 686px;
    height: 392px;
    overflow: hidden;
  }
  .card--front { top: 165px; background: var(--paper); }
  .card--back { top: 653px; background: var(--charcoal); }

  .wordmark {
    position: absolute;
    left: 0;
    right: 0;
    text-align: center;
    font-weight: 700;
    text-transform: uppercase;
    font-size: 46px;
    line-height: 1.02;
    letter-spacing: 0.5px;
  }
  .card--front .wordmark { top: 78px; color: var(--charcoal); }
  .card--back .wordmark { top: 116px; color: var(--emboss); }

  .band {
    position: absolute;
    top: 252px;
    height: 140px;
    box-sizing: border-box;
  }
  .band--identity {
    left: 0;
    width: 345px;
    background: var(--charcoal);
    color: #fff;
    padding: 20px 0 0 41px;
  }
  .band--contact {
    left: 348px;
    right: 0;
    background: var(--orange);
    color: #fff;
    padding: 27px 39px 0 0;
  }
  .person-name {
    margin: 0;
    font-weight: 700;
    font-size: 25px;
    line-height: 1;
    letter-spacing: 0.3px;
  }
  .person-title {
    margin: 3px 0 10px;
    font-size: 17px;
    line-height: 1.1;
  }
  .address {
    margin: 0;
    font-style: normal;
    font-size: 17px;
    line-height: 1.28;
  }
  .contact-list {
    list-style: none;
    margin: 0;
    padding: 0;
    text-align: right;
  }
  .contact-list li {
    display: flex;
    justify-content: flex-end;
    align-items: center;
    gap: 9px;
    font-size: 16.5px;
    line-height: 19.5px;
  }
  .contact-list svg {
    width: 12px;
    height: 12px;
    flex: none;
  }
</style>
</head>
<body>
<main class="canvas">
  <section class="card card--front" aria-label="Business card front">
    <div class="wordmark">Northfield<br>Builders Guild</div>

    <div class="band band--identity">
      <p class="person-name">DANIEL REYES</p>
      <p class="person-title">President</p>
      <address class="address">2400 NW Alder Ave.,<br>Suite #210, Salem, OR 97301</address>
    </div>

    <div class="band band--contact">
      <ul class="contact-list">
        <li>(555) 214-7730
          <svg viewBox="0 0 12 12" aria-hidden="true"><path fill="#fff" d="M2.5 0.8l2 2-1.1 1.4c.7 1.6 2 2.9 3.5 3.6l1.3-1.1 2 2-1.3 1.9C4.8 10.4 1.5 7 0.7 2.1z"/></svg>
        </li>
        <li>555.388.0142
          <svg viewBox="0 0 12 12" aria-hidden="true"><rect x="2.5" y="0.5" width="7" height="11" rx="1" fill="none" stroke="#fff" stroke-width="1.3"/><rect x="4" y="2" width="4" height="7" fill="#fff"/></svg>
        </li>
        <li>support@nbguild.org
          <svg viewBox="0 0 12 12" aria-hidden="true"><rect x="0.5" y="2.5" width="11" height="7" fill="#fff"/><path d="M0.8 3l5.2 3.8L11.2 3" fill="none" stroke="var(--orange)" stroke-width="1"/></svg>
        </li>
        <li>builderslinkguild.org
          <svg viewBox="0 0 12 12" aria-hidden="true"><circle cx="6" cy="6" r="5.5" fill="#fff"/><path d="M3.5 3.5c1 .3 1.5 1 1.2 2s.8 1.5 1.5 1.2M7.5 2.3c.4 1 1.5 1 2 1.9M6.8 8.8c.8-.5 1.8-.3 2.4.4" fill="none" stroke="var(--orange)" stroke-width="1"/></svg>
        </li>
      </ul>
    </div>
  </section>

  <section class="card card--back" aria-label="Business card back">
    <div class="wordmark">Northfield<br>Builders Guild</div>
  </section>
</main>
</body>
</html>
```